ELsewhen website redesign to provide information about experiential workshops, film work and other

We need a redesign of our website elsewhen.org. We conduct experiential workshops of discovery and transformation for individuals and organizations. We need the website to reflect the full extent of ELsewhen programs, and be an information hub for ELsewhen workshops and communities as they develop.

The attached documents contain information about the organization - it's brandbook, copy for web pages, a website layout and a couple of images.

The site is for individuals and companies looking to promote and be change to make a difference. It should be warm, welcoming, and create excitement around the concepts and the ability to discover a new way of being in the world. We are about creating communities around the globe who will embody play, freedom, curiosity and expanded possibilities. We are creating a space for this to happen, both physically (workshops) and online.

We will be on either a SquareSpace, but mos tlikely a Weebly plaform.

Please look at the current site at www.elsewhen.org

Target Market(s)

Initially, are target market will be baby boomers, but will expand to include millennials and students.

Coding

Coded - Design and coding required

Number of Pages Required

5+ page

Requirements
Must have
• The colors, logo and fonts from the brand book.
Nice to have
• Complimentary use of brand colors to create an attractive presentation and energy

```html
<!DOCTYPE html>
<html lang="en">
<head>
<meta charset="utf-8">
<title>ELsewhen – Experiential Workshops</title>
<link rel="stylesheet" href="https://fonts.googleapis.com/css2?family=Poppins:wght@400;500;600;700&family=Arimo:wght@400;700&display=swap">
<style>
:root{
  --orange:#ef5b25;
  --ink:#333333;
  --body:#555555;
  --muted:#666666;
  --light:#f4f4f4;
  --line:#d9d9d9;
  --white:#ffffff;
  --footer:#111111;
}
*{margin:0;padding:0;box-sizing:border-box}
html,body{width:1200px;height:2956px;overflow:hidden}
body{font-family:'Arimo',Arial,sans-serif;color:var(--body);background:var(--white);position:relative}

/* hero */
.hero{position:absolute;left:0;top:0;width:1200px;height:555px;display:flex}
.hero-half{position:relative;height:555px}
.hero-left{width:600px;background:linear-gradient(180deg,#3a3a3a 0%,#262626 60%,#1c1c1c 100%)}
.hero-right{width:600px;background:linear-gradient(160deg,#8a8a8a 0%,#5e5e5e 45%,#3c3c3c 100%)}
.hero-title{position:absolute;top:170px;width:600px;font-family:'Poppins',Arial,sans-serif;font-weight:700;color:var(--white);font-size:56px;line-height:80px;text-align:center;text-transform:uppercase;letter-spacing:.5px}
.hero-left .hero-title{left:22px;width:600px}
.hero-right .hero-title{left:0;letter-spacing:-.5px;font-size:54px}
.hero-btn{position:absolute;top:438px;left:220px;width:174px;height:48px;border:1.5px solid var(--white);border-radius:24px;color:var(--white);font-family:'Poppins',Arial,sans-serif;font-size:14px;text-transform:uppercase;display:flex;align-items:center;justify-content:center;letter-spacing:.3px}

.site-header{position:absolute;left:0;top:0;width:1200px;height:110px;z-index:2}
.brand{position:absolute;left:87px;top:34px;display:flex;align-items:center;gap:10px;font-family:'Poppins',Arial,sans-serif;font-weight:600;font-size:25px;color:var(--white);letter-spacing:1px}
.brand-mark{width:14px;height:14px;background:var(--white)}
.main-nav{position:absolute;right:88px;top:48px;display:flex;gap:20px;font-family:'Poppins',Arial,sans-serif;font-weight:500;font-size:11.5px;color:var(--white);text-transform:uppercase}

/* intro */
.intro{position:absolute;left:0;top:555px;width:1200px;height:574px}
.kicker{font-family:'Poppins',Arial,sans-serif;font-weight:600;color:var(--orange);text-transform:uppercase;text-align:center}
.intro .kicker{position:absolute;top:33px;left:0;width:1200px;font-size:20px}
.section-title{font-family:'Poppins',Arial,sans-serif;font-weight:600;color:var(--ink);text-align:center;text-transform:uppercase}
.intro .section-title{position:absolute;top:68px;left:0;width:1200px;font-size:41px}
.rule{position:absolute;left:560px;width:80px;height:2px;background:var(--ink)}
.intro .rule{top:134px}

.bubble{position:absolute;width:148px;height:148px;border-radius:50%;border:2px solid var(--c)}
.bubble-label{position:absolute;width:220px;text-align:center;font-family:'Poppins',Arial,sans-serif;font-weight:500;font-size:15.5px;line-height:26px;color:var(--ink)}
.stem{position:absolute;width:2px;height:20px;background:var(--c)}
.dot{position:absolute;width:9px;height:9px;border-radius:50%;background:var(--c)}

/* vision */
.vision{position:absolute;left:0;top:1129px;width:1200px;height:467px;background:var(--light)}
.vision-photo{position:absolute;left:0;top:0;width:583px;height:467px;background:linear-gradient(170deg,#6b5a45 0%,#4a3c2e 45%,#2a241e 100%)}
.vision-copy{position:absolute;left:640px;top:90px;width:400px}
.block-title{font-family:'Poppins',Arial,sans-serif;font-weight:500;font-size:37px;color:var(--ink);text-transform:uppercase}
.copy{font-size:12.5px;line-height:26px;color:var(--muted)}
.copy strong{font-family:'Poppins',Arial,sans-serif;font-weight:500;font-size:16px;color:var(--ink)}
.vision .copy{margin-top:28px}

/* what we do */
.what{position:absolute;left:0;top:1596px;width:1200px;height:612px}
.what .section-title{position:absolute;top:0;left:0;width:1200px;font-size:42px;line-height:100px}
.what .rule{top:114px}
.what .kicker-a{position:absolute;top:132px;left:0;width:1200px;font-size:17px}
.what .intro-copy{position:absolute;top:176px;left:235px;width:730px;text-align:center;font-size:12.5px;line-height:28.5px;color:var(--muted)}
.what .intro-copy strong{font-family:'Poppins',Arial,sans-serif;font-weight:500;font-size:15px;color:var(--ink)}
.what .kicker-b{position:absolute;top:282px;left:0;width:1200px;font-size:16.5px}
.movements-sub{position:absolute;top:310px;left:0;width:1200px;text-align:center;font-family:'Poppins',Arial,sans-serif;font-size:15.5px;color:var(--muted);text-transform:uppercase;letter-spacing:.5px}
.movements{position:absolute;top:374px;left:87px;display:flex;gap:13px}
.movement{width:195px;height:177px;border:1.5px solid var(--line);display:flex;flex-direction:column;align-items:center;padding-top:20px}
.movement svg{width:86px;height:86px}
.movement span{margin-top:12px;font-family:'Poppins',Arial,sans-serif;font-size:14px;line-height:21px;color:var(--ink);text-align:center;text-transform:uppercase}

/* stirring the stillness */
.stillness{position:absolute;left:0;top:2208px;width:1200px;height:420px;background:var(--light)}
.stillness-copy{position:absolute;left:85px;top:62px;width:472px}
.stillness .copy{font-size:12px;line-height:27px;margin-top:26px}
.stillness .copy strong{font-family:'Arimo',Arial,sans-serif;font-weight:700;font-size:12.5px}
.stillness-photo{position:absolute;left:625px;top:0;width:575px;height:420px;background:linear-gradient(180deg,#6f7a5e 0%,#5b5a50 40%,#3f3d38 75%,#557043 100%)}

/* community */
.community{position:absolute;left:0;top:2628px;width:1200px;height:258px;text-align:center}
.community .section-title{position:absolute;top:44px;left:0;width:1200px;font-size:38px}
.community .copy{position:absolute;top:110px;left:0;width:1200px;font-size:12.5px;line-height:26px}
.cta{position:absolute;top:183px;left:531px;width:139px;height:44px;border:1.5px solid var(--line);display:flex;align-items:center;justify-content:center;font-family:'Poppins',Arial,sans-serif;font-size:14.5px;color:var(--ink)}

.site-footer{position:absolute;left:0;top:2886px;width:1200px;height:70px;background:var(--footer);color:var(--white);font-size:13px;display:flex;align-items:center;justify-content:center}
</style>
</head>
<body>

<header class="site-header">
  <div class="brand"><span class="brand-mark"></span>ELsewhen</div>
  <nav class="main-nav">
    <span>Home</span><span>About Us</span><span>Workshops</span><span>Projects</span><span>Films</span><span>Store &amp; Resources</span><span>Community</span><span>Contact Us</span>
  </nav>
</header>

<section class="hero">
  <div class="hero-half hero-left" role="img" aria-label="Dark toned photo of a workshop gathering">
    <h1 class="hero-title">What world<br>do we want<br>to live in?</h1>
    <span class="hero-btn">Email Capture</span>
  </div>
  <div class="hero-half hero-right" role="img" aria-label="Grey toned photo of participants sitting on the floor during a workshop">
    <h2 class="hero-title">What kind of<br>life do you want<br>to create?</h2>
    <span class="hero-btn">Member Login</span>
  </div>
</section>

<section class="intro">
  <p class="kicker">Discover an opportunity to live a more dynamic &amp; meaningful life</p>
  <h2 class="section-title">ELsewhen</h2>
  <div class="rule"></div>

  <div class="bubble" style="--c:#c9481c;left:115px;top:173px;background:radial-gradient(circle at 45% 45%,#e8722e,#b5381a 70%,#7c2410)" role="img" aria-label="Warm orange abstract photo representing energy"></div>
  <div class="stem" style="--c:#e0602a;left:188px;top:323px"></div>
  <div class="dot" style="--c:#e0602a;left:184px;top:355px"></div>
  <div class="bubble-label" style="left:79px;top:375px">Moves Energy</div>

  <div class="bubble" style="--c:#b07a86;left:531px;top:173px;background:radial-gradient(circle at 50% 40%,#5a4a7a,#2b2545 60%,#171424)" role="img" aria-label="Deep purple night sky photo representing evolution"></div>
  <div class="stem" style="--c:#9a6a7a;left:604px;top:323px"></div>
  <div class="dot" style="--c:#9a6a7a;left:601px;top:355px"></div>
  <div class="bubble-label" style="left:495px;top:375px">Supports Conscious<br>Evolution</div>

  <div class="bubble" style="--c:#8fc0c0;left:945px;top:173px;background:radial-gradient(circle at 50% 45%,#8fb1a8,#5e8478 65%,#3c5a52)" role="img" aria-label="Teal toned photo of people collaborating"></div>
  <div class="stem" style="--c:#8fc9c9;left:1018px;top:323px"></div>
  <div class="dot" style="--c:#8fc9c9;left:1014px;top:355px"></div>
  <div class="bubble-label" style="left:909px;top:375px">Provides Opportunities<br>for Collaboration &amp;<br>Creation</div>

  <div class="bubble-label" style="left:287px;top:240px">Creates Opportunities<br>for Connecting</div>
  <div class="dot" style="--c:#f0a030;left:394px;top:300px"></div>
  <div class="stem" style="--c:#f0a030;left:397px;top:309px"></div>
  <div class="bubble" style="--c:#f0a030;left:324px;top:346px;background:radial-gradient(circle at 50% 50%,#f7b04a,#e88a22 65%,#c46a14)" role="img" aria-label="Bright orange photo representing connection"></div>

  <div class="bubble-label" style="left:701px;top:240px">Deepens Experience<br>of Life</div>
  <div class="dot" style="--c:#6aa860;left:810px;top:300px"></div>
  <div class="stem" style="--c:#6aa860;left:813px;top:309px"></div>
  <div class="bubble" style="--c:#4f9a52;left:740px;top:346px;background:radial-gradient(circle at 50% 40%,#6f9a5e,#2f5a32 65%,#1a3a1e)" role="img" aria-label="Green toned photo of a figure at a window"></div>
</section>

<section class="vision">
  <div class="vision-photo" role="img" aria-label="Photo of a group seated in a circle inside a wooden cabin"></div>
  <div class="vision-copy">
    <h2 class="block-title">Vision</h2>
    <p class="copy"><strong>We envision a world</strong> in which all people and communities can challenge &amp; <strong>break free</strong> from stories that no longer serve us. We believe that solutions to contemporary challenges will emerge from a place of curiosity, love and connection.</p>
    <p class="copy">Through inspiration, <strong>conscious reflection</strong>, and collaboration, we <strong>take responsibility</strong> for the world <strong>we are manifesting</strong>, and we can discover &amp; create new possibilities for the lives and the society we desire to build.</p>
  </div>
</section>

<section class="what">
  <h2 class="section-title">What we do</h2>
  <div class="rule"></div>
  <p class="kicker kicker-a">ELsewhen Life</p>
  <p class="intro-copy">ELsewhen Life is a workshop designed to re-engage you with life. Through interactive exercises and personal <strong>exploration</strong>, you are taken on a journey that ultimately leaves you experiencing life as a Creator. You will learn to see beliefs and patterns that hold you back in work and relationships as well as a path to transforming the story of your life.</p>
  <p class="kicker kicker-b">ELsewhen Life is a 2-3 day workshop</p>
  <p class="movements-sub">Experienced in 5 movements</p>
  <div class="movements">
    <div class="movement">
      <svg viewBox="0 0 86 86" fill="none" stroke="#333" stroke-width="3" stroke-linecap="round"><circle cx="37" cy="37" r="24"/><path d="M54 54 L76 76"/></svg>
      <span>Curiosity</span>
    </div>
    <div class="movement">
      <svg viewBox="0 0 86 86" fill="none" stroke="#333" stroke-width="3"><circle cx="43" cy="43" r="34"/><circle cx="43" cy="43" r="20"/><circle cx="43" cy="43" r="6" fill="#333"/></svg>
      <span>Awareness</span>
    </div>
    <div class="movement">
      <svg viewBox="0 0 86 86" fill="none" stroke="#333" stroke-width="3" stroke-linecap="round" stroke-linejoin="round"><circle cx="43" cy="43" r="34"/><path d="M28 44 L39 55 L60 32"/></svg>
      <span>Owing your<br>creation</span>
    </div>
    <div class="movement">
      <svg viewBox="0 0 86 86" fill="none" stroke="#333" stroke-width="3" stroke-linecap="round" stroke-linejoin="round"><path d="M70 36 A28 28 0 0 0 18 30"/><path d="M16 50 A28 28 0 0 0 68 56"/><path d="M70 20 V36 H54"/><path d="M16 66 V50 H32"/></svg>
      <span>Reimagining</span>
    </div>
    <div class="movement">
      <svg viewBox="0 0 86 86" fill="none" stroke="#333" stroke-width="3" stroke-linecap="round" stroke-linejoin="round"><path d="M43 76 V12 M22 33 L43 12 L64 33"/><path d="M14 76 H72"/></svg>
      <span>Manifesting</span>
    </div>
  </div>
</section>

<section class="stillness">
  <div class="stillness-copy">
    <h2 class="block-title">Stirring the Stillness</h2>
    <p class="copy">The Stirring the Stillness workshop—an extension of the documentary of the same name—is an <strong>experiential</strong> process to transform participants into challengers of the status quo within themselves, to <strong>enhance</strong> their relationships with others, and to change the environments in which they exist—and ultimately society—for the better.</p>
    <p class="copy">This workshop experience challenges us all to understand the narratives we live within, to look at our current roles in society, and to decide what role we will play to create a more humane, just and peaceful world, for all. It all starts with our willingness to stir the “stillness” of the status quo.</p>
  </div>
  <div class="stillness-photo" role="img" aria-label="Photo of costumed performers and a crowd in front of a barn hung with artworks"></div>
</section>

<section class="community">
  <h2 class="section-title">In your community</h2>
  <p class="copy">Bring ELsewhen or the Stirring the Stillness workshop to your community. We would love to hear from you.<br>Please fill out the brief form here</p>
  <span class="cta">Click Here</span>
</section>

<footer class="site-footer">© Copyright-2018 ELsewhen.All rights reserved.</footer>

</body>
</html>
```